Trading Company needs a business card design, letter head design and email signature

We need a double-sided business card design, letter head design and an email signature. We have a logo design.

Possible Tag Lines:
• “Connecting Worlds, Building Excellence.”
• “Global Sourcing, Local Excellence.”
• “Bridging Borders, Building Quality.”
• “Worldwide Partnerships, Superior Goods.”
• “Where Quality Meets Affordability”

Services Offered:
Procurement
Fabrication
Distribution
Logistics
Import/Export

Requirements
Must have
• Nice quality double sided Business Card design, Letterhead design needs to be A4
Nice to have
• possible ideas on tag lines

```html
<!DOCTYPE html>
<html lang="en">
<head>
<meta charset="utf-8">
<title>Norvane – Business Card</title>
<link rel="stylesheet" href="https://fonts.googleapis.com/css2?family=Open+Sans:wght@400;600;700&display=swap">
<style>
  :root {
    --stage: #2b2d31;
    --card: #222226;
    --red: #ee2326;
    --grey: #6d6e71;
    --white: #ffffff;
    --text-font: "Open Sans", Arial, sans-serif;
  }
  * { box-sizing: border-box; margin: 0; padding: 0; }
  html, body { width: 1200px; height: 780px; overflow: hidden; }
  body {
    background: var(--stage);
    font-family: var(--text-font);
    position: relative;
  }
  .card {
    position: absolute;
    top: 235px;
    width: 540px;
    height: 309px;
    background: var(--card);
    overflow: hidden;
    box-shadow: 0 10px 30px rgba(0,0,0,.45);
  }
  .card--back { left: 40px; }
  .card--front { left: 620px; }

  /* brand lockup */
  .brand {
    display: flex;
    align-items: center;
    gap: 10px;
    color: var(--red);
    font-weight: 700;
    letter-spacing: 3px;
    text-transform: uppercase;
  }
  .brand__square { display: block; background: var(--red); }

  /* back side */
  .card--back .brand { position: absolute; top: 52px; left: 300px; font-size: 30px; }
  .card--back .brand__square { width: 26px; height: 26px; }
  .holder { position: absolute; top: 40px; left: 34px; }
  .holder__name { font-size: 27px; font-weight: 700; line-height: 1.1; }
  .holder__first { color: var(--red); }
  .holder__last { color: var(--grey); }
  .holder__role { color: var(--white); font-size: 15px; margin-top: 4px; }
  .divider {
    position: absolute; left: 215px; top: 150px;
    width: 90px; height: 1px; background: var(--red);
    transform: rotate(-50deg);
  }
  .contacts {
    position: absolute; top: 130px; left: 300px;
    list-style: none; color: var(--white); font-size: 15px;
  }
  .contacts li { display: flex; align-items: center; gap: 10px; line-height: 26px; }
  .contacts svg { width: 14px; height: 14px; flex: none; }
  .services-label {
    position: absolute; bottom: 50px; left: 238px;
    color: var(--red); font-size: 13px; font-weight: 600; letter-spacing: .5px;
  }
  .services {
    position: absolute; left: 0; right: 0; bottom: 0; height: 34px;
    background: var(--red); color: var(--white);
    display: flex; align-items: center; gap: 10px;
    padding: 0 20px; list-style: none; font-size: 14px;
  }
  .services li { display: flex; align-items: center; gap: 10px; }
  .services li::before {
    content: ""; width: 7px; height: 7px; background: var(--white); display: block;
  }

  /* front side */
  .card--front .brand { position: absolute; top: 82px; left: 150px; font-size: 40px; }
  .card--front .brand__square { width: 34px; height: 34px; }
  .taglines {
    position: absolute; top: 165px; left: 30px; right: 20px;
    color: var(--white); font-size: 12.5px; line-height: 22px;
  }
  .taglines p { display: flex; flex-wrap: wrap; align-items: center; gap: 7px; }
  .taglines span { display: flex; align-items: center; gap: 7px; }
  .taglines span::before {
    content: ""; width: 7px; height: 7px; background: var(--red); display: block;
  }
  .taglines p:last-child { padding-left: 90px; }
</style>
</head>
<body>

<section class="card card--back" aria-label="Business card, contact side">
  <div class="holder">
    <p class="holder__name"><span class="holder__first">Tomas</span> <span class="holder__last">Verlin</span></p>
    <p class="holder__role">Managing Director</p>
  </div>

  <div class="brand"><span class="brand__square"></span>Norvane</div>

  <span class="divider"></span>

  <ul class="contacts">
    <li>
      <svg viewBox="0 0 16 16" aria-hidden="true"><path fill="var(--red)" d="M3 1l3 3-2 2c1 2 4 5 6 6l2-2 3 3-2 2C7 15 1 9 1 3z"/></svg>
      (555) 014-2290
    </li>
    <li>
      <svg viewBox="0 0 16 16" aria-hidden="true"><rect x="1" y="3" width="14" height="10" fill="var(--red)"/><path d="M1 3l7 6 7-6" fill="none" stroke="var(--card)" stroke-width="1.5"/></svg>
      hello@norvane-trade.com
    </li>
    <li>
      <svg viewBox="0 0 16 16" aria-hidden="true"><circle cx="8" cy="8" r="7" fill="var(--red)"/><path d="M1 8h14M8 1c-3 4-3 10 0 14M8 1c3 4 3 10 0 14" fill="none" stroke="var(--card)" stroke-width="1"/></svg>
      www.norvane-trade.com
    </li>
  </ul>

  <p class="services-label">SERVICES</p>
  <ul class="services">
    <li>Procurement</li>
    <li>Fabrication</li>
    <li>Distribution</li>
    <li>Logistics</li>
    <li>Import/Export</li>
  </ul>
</section>

<section class="card card--front" aria-label="Business card, brand side">
  <div class="brand"><span class="brand__square"></span>Norvane</div>

  <div class="taglines">
    <p><span>Connecting Worlds, Building Excellence</span><span>Global Sourcing, Local Excellence</span></p>
    <p><span>Bridging Borders, Building Quality</span><span>Worldwide Partnerships, Superior Goods</span></p>
    <p><span>Where Quality Meets Affordability</span></p>
  </div>
</section>

</body>
</html>
```